New Business Card Design Project

Use the flyer uploaded and website www.brightoakbuilders.com for inspiration.
List Our Services on Backside of business cards
Marcus Delling
Harborline Builders Inc.
Licensed General Contractors
858-471-6093

Contact Information for Business Card

Use the flyer uploaded and website www.brightoakbuilders.com for inspiration. List Our Services on Backside of business cards Marcus Delling Harborline Builders Inc. Licensed General Contractors 858-471-6093

```html
<!DOCTYPE html>
<html lang="en">
<head>
<meta charset="utf-8">
<title>Harborline Builders – Business Cards</title>
<link href="https://fonts.googleapis.com/css2?family=Montserrat:wght@400;700&display=swap" rel="stylesheet">
<style>
  :root{
    --bg:#3b3b3b;
    --card:#1d1d1d;
    --ink:#ffffff;
    --muted:#d9d9d9;
    --art-light:#5a5a5a;
    --art-dark:#1a1a1a;
  }
  *{box-sizing:border-box;margin:0;padding:0}
  html,body{width:1200px;height:1200px;overflow:hidden}
  body{
    background:var(--bg);
    font-family:'Montserrat',sans-serif;
    color:var(--ink);
    position:relative;
  }
  .card{
    position:absolute;
    left:162px;
    width:876px;
    height:500px;
    background:var(--card);
    border-radius:26px;
    overflow:hidden;
    box-shadow:0 14px 34px rgba(0,0,0,.45);
  }
  .card--back{top:60px}
  .card--front{top:640px}

  .brand{
    position:absolute;left:50px;top:48px;
    font-size:30px;font-weight:400;letter-spacing:.06em;text-transform:uppercase;
    color:var(--ink);white-space:nowrap;
  }
  .card--front .brand{top:120px}
  .palm-art{
    position:absolute;right:40px;top:150px;
    width:300px;height:320px;
    border-radius:10px;
    background:linear-gradient(160deg,var(--art-light) 0%,#2c2c2c 55%,var(--art-dark) 100%);
    opacity:.8;
  }

  /* back side */
  .services{position:absolute;left:50px;top:150px}
  .services__title{
    font-size:26px;font-weight:700;padding-bottom:8px;
    border-bottom:1.5px solid var(--muted);display:inline-block;padding-right:20px;
  }
  .services__list{list-style:none;margin-top:12px}
  .services__list li{
    font-size:19px;line-height:30px;padding-left:26px;position:relative;color:var(--muted);
  }
  .services__list li::before{
    content:"";position:absolute;left:4px;top:13px;width:6px;height:6px;border-radius:50%;background:var(--ink);
  }

  /* front side */
  .person{position:absolute;right:52px;top:40px;text-align:right;padding-right:26px;z-index:1}
  .person::after{content:"";position:absolute;right:0;top:0;width:12px;height:62px;background:var(--ink)}
  .person__name{font-size:30px;font-weight:700}
  .person__role{font-size:16px;color:var(--muted);margin-top:2px}
  .address{position:absolute;left:110px;top:225px;font-size:19px;line-height:26px;color:var(--muted)}
  .contact{position:absolute;left:110px;top:300px;list-style:none}
  .contact li{display:flex;align-items:center;gap:14px;font-size:19px;line-height:36px;color:var(--muted)}
  .contact svg{width:20px;height:20px;fill:var(--ink);flex:none}
  .license{position:absolute;left:110px;top:432px;font-size:19px;color:var(--muted)}
</style>
</head>
<body>

<section class="card card--back" aria-label="Business card back">
  <div class="brand">Harborline Builders</div>
  <div class="services">
    <h2 class="services__title">Our Services</h2>
    <ul class="services__list">
      <li>Remodel: Kitchen &amp; Bath</li>
      <li>Painting: Interior &amp; Exterior</li>
      <li>Flooring: Carpet, Vinyl, Wood</li>
      <li>Window: Door Replacement</li>
      <li>Plumbing: Repair &amp; Upgrades</li>
      <li>Energy Efficienct Upgrades</li>
      <li>Deck &amp; Patio consturction</li>
      <li>Water &amp; Mold Damage</li>
      <li>Garage Renovation</li>
    </ul>
  </div>
  <div class="palm-art" role="img" aria-label="Dark embossed palm tree and house outline illustration"></div>
</section>

<section class="card card--front" aria-label="Business card front">
  <div class="person">
    <div class="person__name">Marcus Delling</div>
    <div class="person__role">Managing Director</div>
  </div>
  <div class="brand">Harborline Builders</div>
  <div class="palm-art" role="img" aria-label="Dark embossed palm tree and house outline illustration"></div>
  <p class="address">418 Alder Point Road<br>Carlsbad, CA 92008</p>
  <ul class="contact">
    <li>
      <svg viewBox="0 0 24 24" aria-hidden="true"><path d="M6.6 10.8a15.5 15.5 0 0 0 6.6 6.6l2.2-2.2a1 1 0 0 1 1-.25 11.4 11.4 0 0 0 3.6.57 1 1 0 0 1 1 1V20a1 1 0 0 1-1 1A17 17 0 0 1 3 4a1 1 0 0 1 1-1h3.5a1 1 0 0 1 1 1c0 1.25.2 2.45.57 3.57a1 1 0 0 1-.25 1z"/></svg>
      858-471-6093
    </li>
    <li>
      <svg viewBox="0 0 24 24" aria-hidden="true"><path d="M2 5h20v14H2z M2 5l10 8 10-8" fill="none" stroke="#fff" stroke-width="2"/></svg>
      info@brightoakbuilders.com
    </li>
    <li>
      <svg viewBox="0 0 24 24" aria-hidden="true"><circle cx="12" cy="12" r="9" fill="none" stroke="#fff" stroke-width="2"/><path d="M3 12h18M12 3c3 3 3 15 0 18M12 3c-3 3-3 15 0 18" fill="none" stroke="#fff" stroke-width="1.6"/></svg>
      www.brightoakbuilders.com
    </li>
  </ul>
  <p class="license">CSLB Licensed No. #2048517</p>
</section>

</body>
</html>
```